Residential building / Apartments for sale landing page

I need a website / landing page design for my latest development project - a residential building with 70+ apartments for sale. I need the design in layers in Photoshop/Illustrator/InDesign format with all the icons/shapes/maps/graphic assets in vector format (svg, ai, eps) as much as possible.

I prefer white website and please consider the performance/coding experience. We're not making something suitable only for a design contest with fancy parallax effects and confusing animations. We're trying to create usable and clean UI with good UX.

The website will be custom coded, i.e. I'm not using WordPress.

I know that the existing 3D photos are not good but for now you can use them or replace them with some stock photos. I'm going to create new 3D photos soon.

Real Estate Development

1 page

```html
<!DOCTYPE html>
<html lang="en">
<head>
<meta charset="utf-8">
<title>Green Terrace – Apartments for Sale</title>
<link rel="stylesheet" href="https://fonts.googleapis.com/css2?family=Asap+Condensed:wght@500;600;700&family=Montserrat:wght@400;500;600;700&display=swap">
<style>
:root{
  --green:#8dc63f;
  --green-dark:#7ab52f;
  --ink:#1a1a1a;
  --text:#444;
  --muted:#666;
  --light:#f1f1f1;
  --line:#e2e2e2;
  --black:#000;
  --white:#fff;
}
*{box-sizing:border-box;margin:0;padding:0}
html,body{width:1200px;height:4612px;overflow:hidden}
body{position:relative;background:var(--white);font-family:"Montserrat",sans-serif;color:var(--text)}
.abs{position:absolute}
.heading{font-family:"Asap Condensed",sans-serif;font-weight:700;color:var(--ink)}
.rule{position:absolute;height:3px;width:54px;background:var(--green)}
.center{left:0;width:1200px;text-align:center}
.btn{position:absolute;background:var(--green);color:#fff;font-size:12px;font-weight:600;display:flex;align-items:center;justify-content:center;letter-spacing:.5px}
.ph{position:absolute}

/* top bar + header */
.topbar{left:0;top:0;width:1200px;height:39px;background:var(--green);color:#fff;font-size:11px;letter-spacing:.6px}
.topbar span{position:absolute;top:13px}
.brand{display:flex;align-items:center;gap:10px}
.brand-mark{width:22px;height:22px;background:var(--green)}
.brand-name{font-family:"Asap Condensed",sans-serif;font-weight:700;color:var(--ink);letter-spacing:.5px}
.nav{top:74px;right:142px;display:flex;gap:32px;font-size:11.5px;color:var(--ink);letter-spacing:.3px;white-space:nowrap}
.nav .active{color:var(--green)}

/* hero */
.hero-photo{left:440px;top:116px;width:760px;height:538px;background:linear-gradient(160deg,#6f8a5a 0%,#dfe5df 25%,#f3f4f1 45%,#7ea149 70%,#4d6b32 100%)}
.hero-panel{left:0;top:180px;width:609px;height:375px;background:#fff}
.hero-title{left:140px;top:262px;font-size:38px;line-height:45px}
.hero-title em{font-style:normal;color:var(--green)}
.hero-price{left:140px;top:413px;font-size:16px;font-weight:500;color:var(--ink)}

/* project */
.project-frame{left:122px;top:754px;width:408px;height:412px;border:2px solid var(--green)}
.project-photo{left:140px;top:740px;width:404px;height:410px;background:linear-gradient(135deg,#e9e6df,#cfd1cc 50%,#b9b5a9)}
.project-title{left:596px;top:778px;font-size:34px}
.project-copy{left:596px;top:854px;width:462px}
.project-lead{font-size:11px;font-weight:600;line-height:23px;color:var(--ink);margin-bottom:8px}
.project-text{font-size:11px;line-height:23px}
.project-copy .btn-inline{margin-top:22px;width:128px;height:43px;background:var(--green);color:#fff;font-size:12px;font-weight:600;display:flex;align-items:center;justify-content:center;letter-spacing:.5px}

/* facilities */
.facilities{left:0;top:1252px;width:1200px;height:695px;background:var(--light)}
.section-title{font-size:34px}
.fac-grid{left:140px;top:1418px;width:920px;display:grid;grid-template-columns:repeat(5,1fr);gap:16px 13px}
.fac-card{height:214px;background:#fff;text-align:center;padding:30px 10px 0}
.fac-card.is-active{background:var(--green)}
.fac-icon{width:54px;height:40px;margin:0 auto 14px;border-radius:6px;background:#cfe6ad}
.fac-card.is-active .fac-icon{background:#b5da7f}
.fac-name{font-family:"Asap Condensed",sans-serif;font-weight:700;font-size:14px;color:var(--ink);margin-bottom:6px}
.fac-desc{font-size:10px;line-height:18px;color:var(--muted)}
.fac-card.is-active .fac-name,.fac-card.is-active .fac-desc{color:#fff}

/* construction */
.feature-list{left:141px;top:2152px;width:505px;list-style:none}
.feature-list li{position:relative;padding-left:16px;font-size:10px;line-height:16px;color:var(--ink);height:48px}
.feature-list svg{position:absolute;left:0;top:2px}
.build-photo{left:734px;top:2155px;width:324px;height:322px;background:linear-gradient(150deg,#e8ecef,#b2502e 55%,#5b6f3b)}
.people-photo{left:666px;top:2323px;width:194px;height:193px;background:linear-gradient(140deg,#d9d6d0,#8c7a66);border:3px solid #fff}

/* location */
.location{left:0;top:2600px;width:1200px;height:717px;background:var(--light)}
.subtitle{font-size:12px;line-height:20px;color:var(--ink)}
.map-tabs{left:202px;top:2806px;width:796px;height:43px;background:#fff;display:flex}
.map-tab{flex:1;display:flex;align-items:center;justify-content:center;gap:8px;font-size:12px;font-weight:600;color:var(--ink)}
.map-tab.is-active{background:var(--green);color:#fff}
.map-tab i{width:14px;height:12px;border:2px solid currentColor;border-radius:2px;display:block}
.map-area{left:202px;top:2849px;width:796px;height:384px;background:linear-gradient(135deg,#cfe6c4,#e7efd9 40%,#c6e0bd 70%,#d8e8cf)}
.map-card{left:213px;top:2862px;width:269px;height:168px;background:#fff;padding:18px 20px;font-size:11px;color:var(--muted)}
.map-card .dir{color:var(--green-dark);margin-bottom:14px}
.map-card .row{display:flex;justify-content:space-between;border-bottom:1px solid var(--line);padding:7px 0}
.map-card .row:last-child{border:0}

/* gallery */
.gal-photo{top:3509px;width:284px;height:290px}
.gal-box{top:3799px;width:238px;height:89px;border:2px solid var(--green);border-top:0;background:#fff;text-align:center}
.gal-date{margin-top:26px;font-size:16px;font-weight:600;color:var(--ink)}
.gal-view{margin-top:8px;font-size:11px;font-weight:600;color:var(--green)}

/* contact + footer */
.footer{left:0;top:4261px;width:1200px;height:351px;background:var(--black)}
.contact-left{left:140px;top:3972px;width:417px;height:452px;background:var(--light)}
.contact-right{left:557px;top:3972px;width:501px;height:452px;background:var(--green)}
.contact-title{font-size:30px}
.c-item{left:188px;display:flex;align-items:center;gap:22px;font-size:12px;line-height:21px;color:var(--ink)}
.c-icon{width:30px;height:30px;border-radius:50%;background:var(--green);display:flex;align-items:center;justify-content:center;flex:none}
.field{position:absolute;border-bottom:1px solid rgba(255,255,255,.6);font-size:11px;color:#fff;padding-bottom:10px}
.social{width:24px;height:24px;border-radius:50%;display:inline-block}
.foot-nav{top:4492px;left:467px;display:flex;gap:32px;font-size:11px;color:#fff;letter-spacing:.3px;white-space:nowrap}
.copyright{left:467px;top:4534px;font-size:11px;color:#fff}
</style>
</head>
<body>

<!-- Top bar -->
<div class="abs topbar">
  <span style="left:836px">CONTACT</span>
  <span style="left:933px">LANGUAGE: <u>EN</u> | BG</span>
</div>

<!-- Header -->
<div class="abs brand" style="left:140px;top:44px">
  <span class="brand-mark"></span><span class="brand-name" style="font-size:30px">GREEN TERRACE</span>
</div>
<nav class="abs nav">
  <span class="active">GREEN TERRACE</span>
  <span>THE PROJECT</span>
  <span>APARTMENTS/SALES</span>
  <span>LOCATION</span>
  <span>GALLERY</span>
</nav>

<!-- Hero -->
<div class="ph hero-photo" role="img" aria-label="Render of a white residential tower with green planted balconies"></div>
<div class="abs hero-panel"></div>
<h1 class="abs heading hero-title">Sale Of Apartments<br>Directly From The Investor<br>With <em>10% Discount</em></h1>
<p class="abs hero-price">Price from XXX EUR/m2</p>
<div class="btn" style="left:140px;top:455px;width:127px;height:43px">BUY NOW</div>

<!-- The project -->
<div class="abs project-frame"></div>
<div class="ph project-photo" role="img" aria-label="Bright apartment living room with sofa and kitchen"></div>
<h2 class="abs heading project-title">THE PROJECT</h2>
<div class="rule" style="left:596px;top:828px"></div>
<div class="abs project-copy">
  <p class="project-lead">Lorem ipsum dolor sit amet, consectetuer adipiscing elit, sed diam nonummy nibh euismod tincidunt ut laoreet dolore magna aliquam volutpat.</p>
  <p class="project-text">Ut wisi enim ad minim veniam, quis nostrud exerci tation ullamcorper suscipit lobortis nisl ut aliquip ex ea commodo consequat. Duis autem vel eum iriure dolor in hendrerit in vulputate velit esse molestie consequat, vel illum dolore eu feugiat nulla facilisis at vero eros et accumsan et iusto odio dignissim qui blandit praesent luptatum zzril delenit augue duis dolore te feugait nulla facilisi consectetuer adipiscing elit.</p>
  <div class="btn-inline">KNOW MORE</div>
</div>

<!-- Facilities -->
<section class="abs facilities"></section>
<h2 class="abs heading section-title center" style="top:1325px">OUR FACILITIES</h2>
<div class="rule" style="left:573px;top:1377px"></div>
<div class="abs fac-grid">
  <div class="fac-card"><div class="fac-icon" role="img" aria-label="Garden icon"></div><div class="fac-name">Green Areas &amp; Gardens</div><div class="fac-desc">Ut wisi enim ad minim veniam, quis nostrud exerci tation ullamcorper suscipit lobortis nisl ut aliquip.</div></div>
  <div class="fac-card is-active"><div class="fac-icon" role="img" aria-label="Parking icon"></div><div class="fac-name">Parking Spaces</div><div class="fac-desc">Ut wisi enim ad minim veniam, quis nostrud exerci tation ullamcorper suscipit lobortis nisl ut aliquip.</div></div>
  <div class="fac-card"><div class="fac-icon" role="img" aria-label="Bicycle icon"></div><div class="fac-name">Bicycle Parking</div><div class="fac-desc">Ut wisi enim ad minim veniam, quis nostrud exerci tation ullamcorper suscipit lobortis nisl ut aliquip.</div></div>
  <div class="fac-card"><div class="fac-icon" role="img" aria-label="Workout icon"></div><div class="fac-name">Outside Workout Area</div><div class="fac-desc">Ut wisi enim ad minim veniam, quis nostrud exerci tation ullamcorper suscipit lobortis nisl ut aliquip.</div></div>
  <div class="fac-card"><div class="fac-icon" role="img" aria-label="NFC access icon"></div><div class="fac-name">NFC Controlled Access</div><div class="fac-desc">Ut wisi enim ad minim veniam, quis nostrud exerci tation ullamcorper suscipit lobortis nisl ut aliquip.</div></div>
  <div class="fac-card"><div class="fac-icon" role="img" aria-label="Yoga icon"></div><div class="fac-name">Outdoor Yoga Area</div><div class="fac-desc">Ut wisi enim ad minim veniam, quis nostrud exerci tation ullamcorper suscipit lobortis nisl ut aliquip.</div></div>
  <div class="fac-card"><div class="fac-icon" role="img" aria-label="Parasol icon"></div><div class="fac-name">Relaxation Area</div><div class="fac-desc">Ut wisi enim ad minim veniam, quis nostrud exerci tation ullamcorper suscipit lobortis nisl ut aliquip.</div></div>
  <div class="fac-card"><div class="fac-icon" role="img" aria-label="Playground icon"></div><div class="fac-name">Childrens Playground</div><div class="fac-desc">Ut wisi enim ad minim veniam, quis nostrud exerci tation ullamcorper suscipit lobortis nisl ut aliquip.</div></div>
  <div class="fac-card"><div class="fac-icon" role="img" aria-label="Pool icon"></div><div class="fac-name">Pool</div><div class="fac-desc">Ut wisi enim ad minim veniam, quis nostrud exerci tation ullamcorper suscipit lobortis nisl ut aliquip.</div></div>
  <div class="fac-card"><div class="fac-icon" role="img" aria-label="Restaurant icon"></div><div class="fac-name">Restaurant</div><div class="fac-desc">Ut wisi enim ad minim veniam, quis nostrud exerci tation ullamcorper suscipit lobortis nisl ut aliquip.</div></div>
</div>

<!-- Construction features -->
<h2 class="abs heading section-title center" style="top:2025px">CONSTRUCTION FEATURES</h2>
<div class="rule" style="left:573px;top:2078px"></div>
<p class="abs subtitle center" style="top:2100px">Lorem ipsum dolor sit amet, consectetuer adipiscing elit, sed diam nonummy nibh euismod tincidunt.</p>
<ul class="abs feature-list">
  <li><svg width="10" height="10" viewBox="0 0 10 10"><circle cx="5" cy="5" r="5" fill="#8dc63f"/><path d="M2.6 5.1l1.6 1.6 3.2-3.3" stroke="#fff" stroke-width="1.4" fill="none"/></svg>Norvanta Windows – 5 chamber noise reducing glazing with high temperature and noise insulation efficiency</li>
  <li><svg width="10" height="10" viewBox="0 0 10 10"><circle cx="5" cy="5" r="5" fill="#8dc63f"/><path d="M2.6 5.1l1.6 1.6 3.2-3.3" stroke="#fff" stroke-width="1.4" fill="none"/></svg>Halberg bricks – Austrian Halberg Clayform bricks with porous system and 25 cm thick outer walls</li>
  <li><svg width="10" height="10" viewBox="0 0 10 10"><circle cx="5" cy="5" r="5" fill="#8dc63f"/><path d="M2.6 5.1l1.6 1.6 3.2-3.3" stroke="#fff" stroke-width="1.4" fill="none"/></svg>High Ceilings – 2.70m high ceilings giving the light and space you need</li>
  <li><svg width="10" height="10" viewBox="0 0 10 10"><circle cx="5" cy="5" r="5" fill="#8dc63f"/><path d="M2.6 5.1l1.6 1.6 3.2-3.3" stroke="#fff" stroke-width="1.4" fill="none"/></svg>Thermal Insulation System Kelmor – Kelmor Silicone Plaster Thermal Insulation System 10 cm thick and 15 cm thick from the north walls</li>
  <li><svg width="10" height="10" viewBox="0 0 10 10"><circle cx="5" cy="5" r="5" fill="#8dc63f"/><path d="M2.6 5.1l1.6 1.6 3.2-3.3" stroke="#fff" stroke-width="1.4" fill="none"/></svg>Air conditioners – All air conditioners piping systems are installed – ready to plug in the inside and outside body of the aircon system</li>
  <li><svg width="10" height="10" viewBox="0 0 10 10"><circle cx="5" cy="5" r="5" fill="#8dc63f"/><path d="M2.6 5.1l1.6 1.6 3.2-3.3" stroke="#fff" stroke-width="1.4" fill="none"/></svg>HPL ventilated facade Panelux GmbH – Suspended ventilated facade with highly pressed laminated panels by Panelux GmbH in wood color</li>
  <li><svg width="10" height="10" viewBox="0 0 10 10"><circle cx="5" cy="5" r="5" fill="#8dc63f"/><path d="M2.6 5.1l1.6 1.6 3.2-3.3" stroke="#fff" stroke-width="1.4" fill="none"/></svg>Panoramic Aveleta lifts overlooking the park – Giving you the everyday glimpse over the inside garden and putting a smile on your face</li>
  <li><svg width="10" height="10" viewBox="0 0 10 10"><circle cx="5" cy="5" r="5" fill="#8dc63f"/><path d="M2.6 5.1l1.6 1.6 3.2-3.3" stroke="#fff" stroke-width="1.4" fill="none"/></svg>Waterproofing with PVC membrane Durasil – PVC membrane with high puncture and tear resistance, UV resistance and vapor permeability</li>
</ul>
<div class="ph build-photo" role="img" aria-label="Modern apartment block with wooden and brick facade"></div>
<div class="ph people-photo" role="img" aria-label="Buyers meeting an agent in an empty apartment"></div>

<!-- Location -->
<section class="abs location"></section>
<h2 class="abs heading section-title center" style="top:2673px">OUR LOCATION</h2>
<div class="rule" style="left:573px;top:2726px"></div>
<p class="abs subtitle center" style="top:2748px">Lorem ipsum dolor sit amet, consectetuer adipiscing elit, sed diam nonummy nibh euismod tincidunt ut<br>laoreet dolore magna aliquam erat volutpat Ut wisi enim ad minim veniam.</p>
<div class="abs map-tabs">
  <div class="map-tab is-active"><i></i>Schools</div>
  <div class="map-tab"><i></i>Restaurants</div>
  <div class="map-tab"><i></i>Groceries</div>
  <div class="map-tab"><i></i>Coffee</div>
  <div class="map-tab"><i></i>Banks</div>
</div>
<div class="ph map-area" role="img" aria-label="Area map with nearby school locations"></div>
<svg class="abs" style="left:566px;top:3020px" width="40" height="52" viewBox="0 0 40 52"><path d="M20 50C20 50 3 30 3 19a17 17 0 0134 0c0 11-17 31-17 31z" fill="#111"/><circle cx="20" cy="19" r="10" fill="#fff"/></svg>
<svg class="abs" style="left:752px;top:2942px" width="40" height="52" viewBox="0 0 40 52"><path d="M20 50C20 50 3 30 3 19a17 17 0 0134 0c0 11-17 31-17 31z" fill="#111"/><circle cx="20" cy="19" r="10" fill="#fff"/></svg>
<svg class="abs" style="left:808px;top:2996px" width="40" height="52" viewBox="0 0 40 52"><path d="M20 50C20 50 3 30 3 19a17 17 0 0134 0c0 11-17 31-17 31z" fill="#111"/><circle cx="20" cy="19" r="10" fill="#fff"/></svg>
<div class="abs map-card">
  <div class="dir">⌖ Get Direction From</div>
  <div class="row"><span>Consectetuer Adipiscing</span><span>11.20 km</span></div>
  <div class="row"><span>Magna Aliquam</span><span>11.40 km</span></div>
  <div class="row"><span>Sed Diam Nonummy</span><span>15.10 km</span></div>
  <div class="row"><span>Ut Wisi Enim Ad</span><span>18.50 km</span></div>
</div>

<!-- Gallery -->
<h2 class="abs heading section-title center" style="top:3392px">GALLERY</h2>
<div class="rule" style="left:573px;top:3445px"></div>
<p class="abs subtitle center" style="top:3466px">Lorem ipsum dolor sit amet, consectetuer adipiscing elit, sed diam nonummy nibh euismod tincidunt.</p>
<div class="ph gal-photo" style="left:140px;background:linear-gradient(150deg,#e5e5e3,#7a5b3f 55%,#d8d6d2)" role="img" aria-label="Open plan kitchen and living room"></div>
<div class="ph gal-photo" style="left:457px;background:linear-gradient(180deg,#c9dbe8,#8a5d4a 40%,#2a8cc8 75%,#5bb3e0)" role="img" aria-label="Apartment buildings around a swimming pool"></div>
<div class="ph gal-photo" style="left:774px;background:linear-gradient(150deg,#f2f2f0,#c9c7c2 55%,#8f8b84)" role="img" aria-label="Bright living room with large windows"></div>
<div class="abs gal-box" style="left:163px"><div class="gal-date">April 2021</div><div class="gal-view">VIEW ⟶</div></div>
<div class="abs gal-box" style="left:480px"><div class="gal-date">March 2021</div><div class="gal-view">VIEW ⟶</div></div>
<div class="abs gal-box" style="left:797px"><div class="gal-date">February 2021</div><div class="gal-view">VIEW ⟶</div></div>

<!-- Contact -->
<footer class="abs footer"></footer>
<div class="abs contact-left"></div>
<div class="abs contact-right"></div>
<h2 class="abs heading contact-title" style="left:188px;top:4028px">CONTACT DETAILS</h2>
<div class="rule" style="left:188px;top:4080px"></div>
<p class="abs" style="left:188px;top:4108px;width:340px;font-size:11.5px;line-height:22px;color:var(--ink)">Ut wisi enim ad minim veniam, quis nostrud exerci tation ullamcorper suscipit lobortis nisl ut aliquip.</p>
<div class="abs c-item" style="top:4171px"><span class="c-icon"><svg width="14" height="16" viewBox="0 0 14 16"><path d="M7 15s-5-5-5-9a5 5 0 0110 0c0 4-5 9-5 9z" fill="none" stroke="#fff" stroke-width="1.5"/><circle cx="7" cy="6" r="1.8" fill="#fff"/></svg></span><span>123 Lorem ipsum dolor sit amet,<br>consectetuer adipiscing.</span></div>
<div class="abs c-item" style="top:4222px"><span class="c-icon"><svg width="16" height="12" viewBox="0 0 16 12"><rect x="1" y="1" width="14" height="10" fill="none" stroke="#fff" stroke-width="1.5"/><path d="M1 1l7 6 7-6" fill="none" stroke="#fff" stroke-width="1.5"/></svg></span><span>info@greenterrace.com</span></div>
<div class="abs c-item" style="top:4272px"><span class="c-icon"><svg width="14" height="14" viewBox="0 0 14 14"><path d="M3 1l2.5 3-1.5 1.5a8 8 0 004.5 4.5L10 8.5 13 11l-1.5 2C6 13 1 8 1 2.5z" fill="none" stroke="#fff" stroke-width="1.4"/></svg></span><span>123–456–7890</span></div>
<div class="abs" style="left:188px;top:4328px;display:flex;align-items:center;gap:10px;font-size:11px;font-weight:600;color:var(--ink)">FOLLOW US: <span class="social" style="background:#3b5cb8"></span><span class="social" style="background:#55acee"></span></div>

<h2 class="abs heading contact-title" style="left:608px;top:4028px;color:#fff">QUICK INQUIRY</h2>
<div class="rule" style="left:608px;top:4080px;background:#fff"></div>
<div class="field" style="left:608px;top:4110px;width:193px">First Name</div>
<div class="field" style="left:819px;top:4110px;width:193px">Last Name</div>
<div class="field" style="left:608px;top:4164px;width:193px">Phone</div>
<div class="field" style="left:819px;top:4164px;width:193px">Email</div>
<div class="field" style="left:608px;top:4220px;width:404px;height:57px">Message</div>
<div class="btn" style="left:611px;top:4318px;width:123px;height:43px;background:#fff;color:var(--green)">SUBMIT NOW</div>

<!-- Footer -->
<div class="abs brand" style="left:140px;top:4492px">
  <span class="brand-mark"></span><span class="brand-name" style="font-size:36px;color:#fff">GREEN TERRACE</span>
</div>
<nav class="abs foot-nav">
  <span>GREEN TERRACE</span>
  <span>THE PROJECT</span>
  <span>APARTMENTS/SALES</span>
  <span>LOCATION</span>
  <span>GALLERY</span>
</nav>
<p class="abs copyright">Copyright © 2021 Green Terrace. All Rights Reserved.</p>

</body>
</html>
```